Communication and Marketing agency needs a new presentation card

We are a group of communication and marketing agencies specialized in companies that are in the logistics and industrial sector. The head agency is TELVANO Grupo and the group consists of 4 agencies: TELVANO Media, TELVANO Digital, TELVANO Research and DifundeEnPantalla. We hace 4 offices in Spain (Madrid, Barcelona, Valencia and Murcia). We are looking for a clean and attractive design that transmits our experience, brand presence in the market and knowledge to those who receive the card.It has to maintain the colors of the logo that is attached.
Target Market(s)
logistics and industrial sector
Marketing department
Contact Information for Business Card
Clean and attractive design

```html
<!DOCTYPE html>
<html lang="en">
<head>
<meta charset="utf-8">
<title>TELVANO Digital – Business Card</title>
<link rel="stylesheet" href="https://fonts.googleapis.com/css2?family=Open+Sans:wght@400;600&display=swap">
<style>
  :root {
    --stage: #25262b;
    --paper: #ffffff;
    --brand-red: #bd2035;
    --brand-grey: #58585b;
    --logo-grey: #4f4f52;
    --on-red: #ffffff;
  }
  * { margin: 0; padding: 0; box-sizing: border-box; }
  html, body {
    width: 1200px; height: 900px; overflow: hidden;
    background: var(--stage);
    font-family: "Open Sans", Arial, sans-serif;
  }
  .stage {
    position: relative; width: 1200px; height: 900px;
  }
  .card {
    position: absolute; top: 295px;
    width: 540px; height: 310px;
    background: var(--paper);
    overflow: hidden;
    box-shadow: 0 14px 30px rgba(0,0,0,.45);
  }
  .card--front { left: 40px; }
  .card--back  { left: 620px; }
  .card__shapes { position: absolute; inset: 0; width: 100%; height: 100%; }

  .brand-name {
    position: absolute;
    display: flex; align-items: center; gap: 10px;
    color: var(--logo-grey);
    font-weight: 400;
    letter-spacing: 3px;
    white-space: nowrap;
  }
  .brand-name__mark {
    width: 12px; height: 12px; background: var(--brand-red); flex: none;
  }
  .card--front .brand-name { left: 50%; top: 108px; transform: translateX(-50%); font-size: 30px; }
  .card--back .brand-name  { left: 34px; top: 92px; font-size: 21px; letter-spacing: 2px; }

  .card__url {
    position: absolute; left: 0; right: 0; bottom: 14px;
    text-align: center;
    color: var(--on-red); font-size: 13px; letter-spacing: .5px;
  }

  .contact {
    position: absolute; left: 330px; top: 38px;
    color: var(--on-red);
  }
  .contact__name { font-size: 19px; font-weight: 600; letter-spacing: .5px; }
  .contact__role { font-size: 13px; margin-bottom: 20px; }
  .contact__address { font-size: 13px; line-height: 1.45; margin-bottom: 14px; }
  .contact__list { list-style: none; font-size: 13px; }
  .contact__item { display: flex; align-items: center; gap: 8px; height: 22px; }
  .contact__icon { width: 16px; height: 16px; flex: none; }
</style>
</head>
<body>
<main class="stage">

  <section class="card card--front" aria-label="Card front">
    <svg class="card__shapes" viewBox="0 0 540 310" preserveAspectRatio="none" aria-hidden="true">
      <polygon points="440,255 540,205 540,258" fill="var(--brand-grey)"/>
      <polygon points="0,258 440,255 540,230 540,310 0,310" fill="var(--brand-red)"/>
    </svg>
    <div class="brand-name"><span class="brand-name__mark"></span>TELVANO Digital</div>
    <p class="card__url">www.telvanodigital.com</p>
  </section>

  <section class="card card--back" aria-label="Card back">
    <svg class="card__shapes" viewBox="0 0 540 310" preserveAspectRatio="none" aria-hidden="true">
      <polygon points="254,0 294,0 280,140" fill="var(--brand-grey)"/>
      <polygon points="294,0 540,0 540,310 238,310 280,140" fill="var(--brand-red)"/>
    </svg>
    <div class="brand-name"><span class="brand-name__mark"></span>TELVANO Digital</div>

    <div class="contact">
      <p class="contact__name">MARCELO IBARRA</p>
      <p class="contact__role">CEO</p>
      <p class="contact__address">1450 Harbor Ave<br>Linden Falls, OR 97210</p>
      <ul class="contact__list">
        <li class="contact__item">
          <svg class="contact__icon" viewBox="0 0 16 16" aria-hidden="true"><circle cx="8" cy="8" r="8" fill="var(--brand-grey)"/><path d="M5.2 4.2l1.5-.3.8 1.8-1 .8a5 5 0 0 0 2.9 2.9l.8-1 1.8.8-.3 1.5c-3.8.3-6.8-2.7-6.5-6.5z" fill="#fff"/></svg>
          555.014.2187
        </li>
        <li class="contact__item">
          <svg class="contact__icon" viewBox="0 0 16 16" aria-hidden="true"><circle cx="8" cy="8" r="8" fill="var(--brand-grey)"/><rect x="5.5" y="4" width="5" height="3" fill="#fff"/><rect x="4" y="7" width="8" height="4" rx="1" fill="#fff"/><rect x="5.5" y="10" width="5" height="2.5" fill="#fff" stroke="var(--brand-grey)" stroke-width=".6"/></svg>
          555.014.2120
        </li>
        <li class="contact__item">
          <svg class="contact__icon" viewBox="0 0 16 16" aria-hidden="true"><circle cx="8" cy="8" r="8" fill="var(--brand-grey)"/><rect x="4" y="5" width="8" height="6" fill="#fff"/><path d="M4 5l4 3.3L12 5" fill="none" stroke="var(--brand-grey)" stroke-width=".9"/></svg>
          info@telvanodigital.com
        </li>
        <li class="contact__item">
          <svg class="contact__icon" viewBox="0 0 16 16" aria-hidden="true"><circle cx="8" cy="8" r="8" fill="var(--brand-grey)"/><circle cx="8" cy="8" r="4" fill="none" stroke="#fff" stroke-width="1"/><path d="M4 8h8M8 4c-2 2.4-2 5.6 0 8M8 4c2 2.4 2 5.6 0 8" fill="none" stroke="#fff" stroke-width=".8"/></svg>
          www.telvanodigital.com
        </li>
      </ul>
    </div>
  </section>

</main>
</body>
</html>
```